verdant terraces simple classy business card design

my name is colin barrow and I run a gardening business aimed at high class verdant terraces. the business name is verdant terraces and our logo was designed on pixel harbour .My clientel are anything from residential homes to businesses. I take pride in my work and know that I offer a service like no other in my area.
The business card will be used to represent my business and I want it to be not only rememberable, but simplistic and modern. Eye catching too. Of course I would like it relatable to gardening and appealing to the correct clientel - those being garden enthusiasts, prestigious homes and businesses that are after top of the line gardening services like no other on the market.
I am not a typical lawn mowing business so I don't want a typical card design that represents that. The gardens I work with are generally million dollar properties with owners who are very garden proud looking for upkeep and guidance from me along with sometimes whole new garden designs. I want the business cards to show to my clients that I take pride, as they do, in their garden. And I want them to know from my card that I am a professional, qualified horticulturist offering them a top of the line service for life. I want them to refer my business on. I want them to look at my business card and see class and professionalism in a modern unique bold way.
The card should be simple with the possibility of the logo on the front being embossed/debossed and my details on the back the card should have a organic garden feel it's very important to me that it is absolutely perfect
I am also very open to ideas and suggestions so look forward to seeing the designs. the business logo has been supplied with this project and I want the card to be double sided

Contact info is
Colin Barrow - Managing Director / Horticulturist
Phone : 0481 526 704
Email: colinbarrow@verdantterraces.example.au

Target Market(s)

high class gardens residential and commercial

Industry/Entity Type

Gardener

Contact Information for Business Card

Contact info is
Phone : 0481 526 704

PLEASE MAKE CARD DOUBLE SIDED

Requirements
Must have
• organic simple classy modern feel
• must flow with the current logo that has been supplied with this project
• Double sided
• Must explain in a simple way that I deal with high end gardens and I'm a qualified horticulturist
Nice to have
• embossed debossed logo
Should not have
• shouldn't be to busy or cheap looking

```html
<!DOCTYPE html>
<html lang="en">
<head>
<meta charset="utf-8">
<title>Verdant Terraces – Business Card</title>
<link href="https://fonts.googleapis.com/css2?family=Cinzel:wght@500&family=PT+Sans:wght@400&display=swap" rel="stylesheet">
<style>
  :root {
    --bg: #efefed;
    --card-green: #669c58;
    --gold: #c9a43c;
    --white: #ffffff;
    --sky: #2f6fc0;
    --stone: #d8c3a4;
    --hedge: #3f7a2a;
    --hedge-dark: #2c5a1f;
  }
  html, body {
    margin: 0;
    padding: 0;
    width: 1200px;
    height: 854px;
    overflow: hidden;
    background: var(--bg);
  }
  .canvas {
    position: relative;
    width: 1200px;
    height: 854px;
  }
  .card {
    position: absolute;
    box-shadow: 0 2px 6px rgba(0,0,0,0.18);
  }
  /* Back: contact details */
  .card-back {
    left: 195px;
    top: 176px;
    width: 302px;
    height: 527px;
    background: var(--card-green);
    color: var(--white);
    font-family: "PT Sans", sans-serif;
    text-align: center;
  }
  .brand {
    position: absolute;
    left: 0;
    width: 100%;
    font-family: "Cinzel", serif;
    font-weight: 500;
    color: var(--gold);
    text-align: center;
    line-height: 1;
  }
  .brand-mark {
    display: block;
    margin: 0 auto;
    border-radius: 50%;
    background: var(--gold);
  }
  .card-back .brand { top: 86px; font-size: 23px; }
  .card-back .brand-mark { width: 48px; height: 48px; margin-bottom: 14px; }
  .brand-line { display: block; letter-spacing: 1px; }
  .brand-line + .brand-line { margin-top: 6px; letter-spacing: 5px; }
  .divider {
    position: absolute;
    left: 26px;
    top: 272px;
    width: 250px;
    height: 2px;
    background: var(--gold);
  }
  .person-name {
    position: absolute;
    top: 316px;
    width: 100%;
    margin: 0;
    font-size: 24px;
    font-weight: 400;
  }
  .person-title {
    position: absolute;
    top: 359px;
    width: 100%;
    margin: 0;
    font-size: 13.5px;
  }
  .contact {
    position: absolute;
    top: 431px;
    width: 100%;
    margin: 0;
    font-size: 12px;
    line-height: 17px;
  }
  /* Front: garden view with logo panel */
  .card-front {
    left: 564px;
    top: 275px;
    width: 528px;
    height: 301px;
    background: var(--card-green);
  }
  .garden-view {
    position: absolute;
    left: 4px;
    top: 4px;
    right: 5px;
    bottom: 11px;
    background: linear-gradient(to bottom,
      var(--sky) 0%, var(--stone) 8%, #e2cfb2 34%, #e9e4d6 40%,
      var(--hedge) 48%, #5b8c3a 62%, var(--hedge-dark) 78%, var(--hedge) 94%, #8d9a8c 100%);
  }
  .logo-panel {
    position: absolute;
    left: 171px;
    top: 0;
    width: 173px;
    height: 112px;
    background: var(--card-green);
  }
  .card-front .brand { top: 20px; font-size: 16px; }
  .card-front .brand-mark { width: 34px; height: 34px; margin-bottom: 10px; }
  .card-front .brand-line + .brand-line { margin-top: 4px; letter-spacing: 3px; }
</style>
</head>
<body>
<main class="canvas">
  <section class="card card-back" aria-label="Business card, back">
    <div class="brand">
      <span class="brand-mark"></span>
      <span class="brand-line">VERDANT</span>
      <span class="brand-line">TERRACES</span>
    </div>
    <div class="divider"></div>
    <h1 class="person-name">Colin Barrow</h1>
    <p class="person-title">Managing Director / Horticulturist</p>
    <p class="contact">Phone : 0481 526 704<br>Email: colinbarrow@verdantterraces.example.au</p>
  </section>

  <section class="card card-front" aria-label="Business card, front">
    <div class="garden-view" role="img" aria-label="Photograph of a formal terraced garden with clipped hedges and stone steps below a grand manor house"></div>
    <div class="logo-panel">
      <div class="brand">
        <span class="brand-mark"></span>
        <span class="brand-line">VERDANT</span>
        <span class="brand-line">TERRACES</span>
      </div>
    </div>
  </section>
</main>
</body>
</html>
```